Need Help having my business card stand out

I am the owner of Birchway Canine Training and would like for my business cards to stand out. I have been trying to keep designing them myself but I can't get what I have in my head on the card. I will try my best to post templates that I like for inspirations. I want something unique but elegant. I don't want in to look cartoony or cheesy. It needs to pop in a pet shop but also in a coffee shop or gym.

Target Market(s)

Dog owners, Married ,No young kids Jr High school kids and up (maybe kids on the way) Executives, Stay at home moms/wives, Small business owners

Industry/Entity Type

Dog Training

Contact Information for Business Card

Lowell Spratt, 281-904-3376, info@birchwaycanine.example, www.birchwaycanine.example

Colors

Designer to choose colors to be used in the design.

Requirements
Must have
• my logo
Should not have
• Cursive lettering

```html
<!DOCTYPE html>
<html lang="en">
<head>
<meta charset="utf-8">
<title>Birchway Canine Training – Business Card</title>
<link rel="stylesheet" href="https://fonts.googleapis.com/css2?family=Open+Sans:wght@400;700&display=swap">
<style>
  :root {
    --page: #ecebe8;
    --charcoal: #2b2b2d;
    --slate: #5a5a5c;
    --slate-deep: #424244;
    --white: #ffffff;
    --muted: #8a8a8c;
    --ring: #6b6b6d;
    --photo-top: #cfd6c4;
    --photo-mid: #9a7f62;
    --photo-low: #6f8a4c;
  }
  * { box-sizing: border-box; margin: 0; padding: 0; }
  html, body {
    width: 1200px; height: 894px; overflow: hidden;
    background: var(--page);
    font-family: "Open Sans", sans-serif;
  }
  .card {
    position: absolute; left: 320px;
    width: 560px; height: 320px;
    overflow: hidden;
    box-shadow: 0 6px 18px rgba(0,0,0,.18);
  }
  .card--front { top: 97px; background: var(--charcoal); }
  .card--back  { top: 477px; background: var(--charcoal); }

  .front__photo {
    position: absolute; left: 0; top: 0;
    width: 228px; height: 100%;
    background: linear-gradient(160deg, var(--photo-top) 0%, var(--photo-mid) 55%, var(--photo-low) 100%);
  }
  .front__badge {
    position: absolute; left: 278px; top: 30px;
    width: 260px; height: 260px; border-radius: 50%;
    background: var(--white);
    border: 7px solid var(--ring);
    display: flex; align-items: center; justify-content: center;
    text-align: center; padding: 30px;
  }
  .front__name {
    font-weight: 700; font-size: 30px; line-height: 1.15;
    color: var(--charcoal);
  }

  .back__info {
    position: absolute; left: 0; top: 0; width: 320px; height: 100%;
    padding: 40px 0 0 32px;
  }
  .back__name { font-weight: 700; font-size: 30px; color: var(--white); line-height: 1.1; }
  .back__role { font-size: 18px; color: var(--muted); margin-top: 2px; }
  .back__contacts {
    position: absolute; left: 32px; bottom: 28px;
    list-style: none;
  }
  .back__contacts li {
    display: flex; align-items: center; gap: 14px;
    font-size: 15px; color: var(--muted); margin-top: 8px;
  }
  .back__contacts svg { width: 14px; height: 14px; fill: none; stroke: var(--muted); stroke-width: 1.6; }
  .back__panel {
    position: absolute; left: 320px; top: 0; width: 240px; height: 100%;
    background: var(--slate);
  }
  .back__mark {
    position: absolute; left: 20px; top: 60px; width: 200px;
    font-weight: 700; font-size: 32px; line-height: 1.1;
    color: var(--slate-deep); text-align: center;
  }
  .back__social {
    position: absolute; left: 20px; bottom: 34px;
    display: flex; align-items: center; gap: 6px;
  }
  .social-dot { width: 18px; height: 18px; background: var(--slate-deep); }
  .back__handle { font-size: 14px; color: var(--muted); margin-left: 8px; }
</style>
</head>
<body>
  <section class="card card--front">
    <div class="front__photo" role="img" aria-label="Photo of the trainer kneeling on grass with a shepherd dog in a wooded park"></div>
    <div class="front__badge">
      <span class="front__name">Birchway Canine Training</span>
    </div>
  </section>

  <section class="card card--back">
    <div class="back__info">
      <h1 class="back__name">Lowell Spratt</h1>
      <p class="back__role">dog trainer</p>
      <ul class="back__contacts">
        <li>
          <svg viewBox="0 0 14 14"><path d="M3 1.5l2 2.5-1.2 1.4c.8 1.7 2 2.9 3.8 3.8L9 8l2.5 2-1.2 2.2C6 12 2 8 1.8 3z"/></svg>
          281-904-3376
        </li>
        <li>
          <svg viewBox="0 0 14 14"><rect x="1" y="3" width="12" height="8"/><path d="M1 3l6 5 6-5"/></svg>
          info@birchwaycanine.example
        </li>
        <li>
          <svg viewBox="0 0 14 14"><circle cx="7" cy="7" r="5.5"/><path d="M1.5 7h11M7 1.5c2.5 3 2.5 8 0 11M7 1.5c-2.5 3-2.5 8 0 11"/></svg>
          www.birchwaycanine.example
        </li>
      </ul>
    </div>
    <div class="back__panel">
      <div class="back__mark">Birchway Canine Training</div>
      <div class="back__social">
        <span class="social-dot"></span>
        <span class="social-dot"></span>
        <span class="social-dot"></span>
        <span class="back__handle">birchwaycanine</span>
      </div>
    </div>
  </section>
</body>
</html>
```